The Harbourlight Dental centre, the Zorvik of dentistry

New concept of running a dental practice by having a walk in practice
WE ARE A HUSBAND AND WIFE TEAM

Really modern and sophisticated, we want it to feel different from the traditional dental practice.
we want it split into different pages:CONTACT US
LOCATION: Information about our location since patients often confuse us with the practice across the road
ABOUT US:
Opening hours - & 7 Days, We offer a weekend service
WALK IN: We offer a walk in service for dental treatments
TREATMENTS we offer

DENTAL ADVICE: Free dentist advise call back- So a dentist will call you back for free to discuss

Target Market(s)

Everyone

Industry/Entity Type

Dental

Coding

Coded - Design and coding required

Number of Pages Required

5+ page

Requirements
Must have
• First page
• * changing pictures
• *opening times
• * our walk in concept I.e. no appointment needed
• *logo
• * links in to clinic tidal (online booking system in Australia)
• * address /phone number/email
• * possible videos
• Second page
• meet the team
• third page
• dental treatments/walk in treatments
• fourth page
• dental advice with vid larko videos
• Fifth page
• contact us/maps/ we get confused with the dental practice across the road
• We would also like a giving back page. In this please include the photo's below of our dental mission in Guatemala, where by we did treatment for patients as part of a charity.
Nice to have
• Changing pictures on the home screen
• videos linked to home page

```html
<!DOCTYPE html>
<html lang="en">
<head>
<meta charset="utf-8">
<title>Dental Advice – The Harbourlight Dental centre</title>
<link href="https://fonts.googleapis.com/css2?family=Open+Sans:wght@300;400;600&display=swap" rel="stylesheet">
<style>
:root{
  --green:#a5cb3f;
  --green-dark:#93b933;
  --blue:#1fa3dc;
  --text:#333;
  --muted:#666;
  --faint:#999;
  --panel:#f1f1f1;
  --contact-bg:#ebebeb;
  --dark:#3a3a3a;
  --darker:#2d2d2d;
  --white:#fff;
}
*{box-sizing:border-box;margin:0;padding:0}
html,body{width:838px;height:1200px;overflow:hidden}
body{font-family:"Open Sans",Arial,sans-serif;color:var(--text);background:var(--white);position:relative}
.wrap{width:653px;margin:0 auto;position:relative}

.top-bar{height:3px;background:linear-gradient(90deg,var(--green) 0 50%,var(--blue) 50% 100%)}

.site-header{height:127px;border-bottom:4px solid #ececec}
.brand{position:absolute;left:0;top:28px;display:flex;align-items:center;gap:8px}
.brand-dot{width:26px;height:26px;border-radius:50%;background:var(--blue)}
.brand-name{font-size:15px;font-weight:600;color:var(--green)}
.header-info{position:absolute;right:0;top:30px;text-align:right;font-size:6.5px;color:var(--muted)}
.header-info .row{display:flex;justify-content:flex-end;gap:12px;align-items:center}
.header-info .row span{display:inline-flex;align-items:center;gap:3px}
.header-contact{margin-top:6px;font-size:11.5px;color:var(--blue);gap:14px!important}
.header-contact span{gap:5px!important}

.main-nav{position:absolute;left:0;top:85px;width:653px;height:37px;background:linear-gradient(var(--green),var(--green-dark));display:flex;align-items:stretch}
.main-nav a{color:var(--white);text-decoration:none;font-size:8px;display:flex;align-items:center;padding:0 0;justify-content:center}
.main-nav .active{background:var(--blue)}

.advice{height:280px;padding-top:25px}
.section-title{font-weight:300;color:var(--green);font-size:22px}
.advice-grid{position:relative;margin-top:8px;height:190px}
.video{position:absolute;background:linear-gradient(135deg,#4a4f6a,#2f3142 60%,#5a4a48);display:flex;align-items:center;justify-content:center}
.video-main{left:0;top:0;width:326px;height:190px}
.video-s1{left:335px;top:1px;width:128px;height:89px;background:linear-gradient(135deg,#54565c,#34363d)}
.video-s2{left:335px;top:101px;width:128px;height:89px;background:linear-gradient(135deg,#3f4660,#6b6a72)}
.play{width:27px;height:27px}
.video-s1 .play,.video-s2 .play{width:26px;height:26px}
.video-copy{position:absolute;left:474px;width:180px}
.video-copy h3{font-weight:400;font-size:11.5px;color:var(--blue);margin-bottom:6px}
.video-copy p{font-size:7.3px;line-height:13.5px;color:#555}

.articles{height:319px;background:var(--panel);padding-top:20px}
.articles .section-title{text-align:center}
.cards{display:flex;gap:12.5px;margin-top:15px}
.card{width:154px;height:223px;background:var(--white)}
.card-photo{height:100px}
.card-1 .card-photo{background:linear-gradient(135deg,#8a7a6a,#4d5a6e)}
.card-2 .card-photo{background:linear-gradient(135deg,#d8d2c6,#3e6a5a)}
.card-3 .card-photo{background:linear-gradient(135deg,#e6e8ea,#9ccb4a 70%,#cfd4d8)}
.card-4 .card-photo{background:linear-gradient(135deg,#f2f3f3,#dfe3e4 55%,#3aa040)}
.card h4{font-weight:400;font-size:9.5px;line-height:14px;color:#222;padding:9px 8px 5px}
.card p{font-size:6.4px;line-height:11.2px;color:var(--faint);padding:0 8px}

.callback{height:129px;background:var(--green);text-align:center;padding-top:15px}
.callback h2{font-weight:400;color:var(--white);font-size:23px;line-height:27px}
.callback-form{display:flex;gap:6px;justify-content:center;margin-top:10px}
.field{background:var(--white);height:31px;display:flex;align-items:center;padding-left:12px;font-size:8px;color:#888;width:162px}
.btn{background:var(--darker);color:var(--white);font-size:9px;display:flex;align-items:center;justify-content:center;height:31px}
.callback .btn{width:57px}

.screen{height:69px;display:flex;align-items:center;justify-content:center;gap:8px}
.screen-dot{width:14px;height:14px;border-radius:50%;background:var(--green)}
.screen h2{font-weight:400;color:var(--blue);font-size:23px}

.find-us{height:172px;display:flex}
.map{width:418px;height:172px;background:linear-gradient(135deg,#d9d9d9,#c9c9c9 50%,#dedede)}
.contact-panel{flex:1;background:var(--contact-bg);padding:22px 0 0 35px}
.contact-panel h3{font-weight:400;font-size:16px;color:#222;margin-bottom:10px}
.contact-grid{display:grid;grid-template-columns:127px 127px;gap:8px 7px}
.contact-grid .field{width:127px;height:26px;font-size:8px}
.contact-grid .btn{height:26px;font-size:8px}

.site-footer{height:101px;background:var(--dark);color:#ccc}
.footer-row{display:flex;align-items:center;height:44px;font-size:7.5px;gap:0;border-bottom:1px solid #555}
.footer-row span{display:inline-flex;align-items:center;gap:6px}
.footer-row .addr{width:246px}
.footer-row .call{width:132px}
.footer-row .mail{flex:1}
.social{display:flex;gap:9px}
.social i{width:9px;height:9px;border-radius:50%;border:1px solid #888;display:block}
.footer-links{font-size:6.5px;margin-top:12px;color:#ccc}
.footer-copy{font-size:6.5px;margin-top:9px}
.booking{position:absolute;right:0;top:58px;display:flex;align-items:center;gap:10px;font-size:6.5px}
.booking-name{display:flex;align-items:center;gap:5px;font-size:14px;color:#bbb}
.booking-name i{width:14px;height:14px;background:#888;display:block}
</style>
</head>
<body>
<div class="top-bar"></div>

<header class="site-header">
  <div class="wrap">
    <div class="brand"><span class="brand-dot"></span><span class="brand-name">The Harbourlight Dental centre</span></div>
    <div class="header-info">
      <div class="row">
        <span><svg width="6" height="7" viewBox="0 0 10 12"><path d="M5 0a4 4 0 0 0-4 4c0 3 4 8 4 8s4-5 4-8a4 4 0 0 0-4-4zm0 5.5A1.5 1.5 0 1 1 5 2.5a1.5 1.5 0 0 1 0 3z" fill="#666"/></svg>Unit 7, 18 Saltmarsh Parade, Coralbrook, WA 6099.</span>
        <span><svg width="7" height="7" viewBox="0 0 10 10"><circle cx="5" cy="5" r="4" fill="none" stroke="#666" stroke-width="1.3"/><path d="M5 2.5V5h2" fill="none" stroke="#666"/></svg>OPEN 8 AM TO 8PM 7 DAYS A WEEK</span>
      </div>
      <div class="row header-contact">
        <span><svg width="10" height="10" viewBox="0 0 12 12"><path d="M2.5 0.5l2 2.5-1.2 1.3a7 7 0 0 0 4.4 4.4L9 7.5l2.5 2-1.3 2C5 11.5.5 7 .5 1.8z" fill="#1fa3dc"/></svg>08 5550 1427</span>
        <span><svg width="12" height="9" viewBox="0 0 12 9"><rect width="12" height="9" rx="1" fill="#1fa3dc"/><path d="M0.5 0.8L6 5l5.5-4.2" fill="none" stroke="#fff" stroke-width="1"/></svg>info@harbourlightdental.com</span>
      </div>
    </div>
    <nav class="main-nav">
      <a style="width:100px">HOME</a>
      <a style="width:95px">MEET THE TEAM</a>
      <a style="width:223px">DENTAL TREATMENTS/WALK-IN TREATMENTS</a>
      <a class="active" style="width:100px">DENTAL ADVICE</a>
      <a style="width:135px">CONTACT US</a>
    </nav>
  </div>
</header>

<section class="advice">
  <div class="wrap">
    <h1 class="section-title">Dental Advice</h1>
    <div class="advice-grid">
      <div class="video video-main" role="img" aria-label="Video still: dentists treating a patient in a clinic">
        <svg class="play" viewBox="0 0 30 30"><circle cx="15" cy="15" r="14" fill="#fff"/><circle cx="15" cy="15" r="11" fill="#1fa3dc"/><path d="M12 9.5l8 5.5-8 5.5z" fill="#fff"/></svg>
      </div>
      <div class="video video-s1" role="img" aria-label="Video still: patients waiting at a dental mission">
        <svg class="play" viewBox="0 0 30 30"><circle cx="15" cy="15" r="14" fill="#fff"/><circle cx="15" cy="15" r="11" fill="#1fa3dc"/><path d="M12 9.5l8 5.5-8 5.5z" fill="#fff"/></svg>
      </div>
      <div class="video video-s2" role="img" aria-label="Video still: dental treatment in progress">
        <svg class="play" viewBox="0 0 30 30"><circle cx="15" cy="15" r="14" fill="#fff"/><circle cx="15" cy="15" r="11" fill="#1fa3dc"/><path d="M12 9.5l8 5.5-8 5.5z" fill="#fff"/></svg>
      </div>
      <div class="video-copy" style="top:0">
        <h3>Phasellus nisl est, condimentum</h3>
        <p>Aliquam erat volutpat. Quisque aliquet ex nec est vestibulum pulvinar. Pellentesque convallis molestie enim sit amet efficitur. Etiam id imper-diet lectus. Vivamus lacus justo, ultrices nec erat in, euismod iaculis mauris.</p>
      </div>
      <div class="video-copy" style="top:101px">
        <h3>Nunc sit amet consequat risus</h3>
        <p>Aliquam erat volutpat. Quisque aliquet ex nec est vestibulum pulvinar. Pellentesque convallis molestie enim sit amet efficitur. Etiam id imper-diet lectus. Vivamus lacus justo, ultrices nec erat in, euismod iaculis mauris.</p>
      </div>
    </div>
  </div>
</section>

<section class="articles">
  <div class="wrap">
    <h2 class="section-title">Articles</h2>
    <div class="cards">
      <article class="card card-1"><div class="card-photo" role="img" aria-label="Photo: mother and child at a dental mission"></div><h4>Aenean sed quam non sapien at faucibus consequat vitae</h4><p>Donec vestibulum odio sem, ac laoreet massa ullamcorper id. Donec molestie nisi et tellus hendrerit vehicula. Nunc eu ligula sed quam pulvinar maximus in vitae eros. Proin porta fermentum ipsum, vel porttitor turpis venenatis luctus.</p></article>
      <article class="card card-2"><div class="card-photo" role="img" aria-label="Photo: the dentist couple in scrubs at a charity mission"></div><h4>Aenean sed quam non sapien at faucibus consequat vitae</h4><p>Donec vestibulum odio sem, ac laoreet massa ullamcorper id. Donec molestie nisi et tellus hendrerit vehicula. Nunc eu ligula sed quam pulvinar maximus in vitae eros. Proin porta fermentum ipsum, vel porttitor turpis venenatis luctus.</p></article>
      <article class="card card-3"><div class="card-photo" role="img" aria-label="Photo: green dental chair in a treatment room"></div><h4>Aenean sed quam non sapien at faucibus consequat vitae</h4><p>Donec vestibulum odio sem, ac laoreet massa ullamcorper id. Donec molestie nisi et tellus hendrerit vehicula. Nunc eu ligula sed quam pulvinar maximus in vitae eros. Proin porta fermentum ipsum, vel porttitor turpis venenatis luctus.</p></article>
      <article class="card card-4"><div class="card-photo" role="img" aria-label="Photo: clinic reception desk with green wall"></div><h4>Aenean sed quam non sapien at faucibus consequat vitae</h4><p>Donec vestibulum odio sem, ac laoreet massa ullamcorper id. Donec molestie nisi et tellus hendrerit vehicula. Nunc eu ligula sed quam pulvinar maximus in vitae eros. Proin porta fermentum ipsum, vel porttitor turpis venenatis luctus.</p></article>
    </div>
  </div>
</section>

<section class="callback">
  <h2>Enter your details for our Doctors Call Back for<br>Free to discuss any tooth concerns you may have</h2>
  <div class="callback-form">
    <div class="field">Name</div>
    <div class="field">Email</div>
    <div class="field">Phone</div>
    <div class="btn">SUBMIT</div>
  </div>
</section>

<section class="screen">
  <span class="screen-dot"></span>
  <h2>We also offer a Free Oral Cancer Screen</h2>
</section>

<section class="find-us">
  <div class="map" role="img" aria-label="Grey world map showing the clinic location"></div>
  <div class="contact-panel">
    <h3>Contact Us</h3>
    <div class="contact-grid">
      <div class="field">First Name</div>
      <div class="field">Last Name</div>
      <div class="field">Phone</div>
      <div class="field">Email</div>
      <div class="field">City</div>
      <div class="btn">SUBMIT</div>
    </div>
  </div>
</section>

<footer class="site-footer">
  <div class="wrap">
    <div class="footer-row">
      <span class="addr"><svg width="7" height="9" viewBox="0 0 10 12"><path d="M5 0a4 4 0 0 0-4 4c0 3 4 8 4 8s4-5 4-8a4 4 0 0 0-4-4zm0 5.5A1.5 1.5 0 1 1 5 2.5a1.5 1.5 0 0 1 0 3z" fill="#bbb"/></svg>Unit 7, 18 Saltmarsh Parade, Coralbrook, WA 6099</span>
      <span class="call"><svg width="8" height="8" viewBox="0 0 12 12"><path d="M2.5 0.5l2 2.5-1.2 1.3a7 7 0 0 0 4.4 4.4L9 7.5l2.5 2-1.3 2C5 11.5.5 7 .5 1.8z" fill="#bbb"/></svg>Call Now: 08 5550 1427</span>
      <span class="mail"><svg width="11" height="8" viewBox="0 0 12 9"><rect width="12" height="9" rx="1" fill="#bbb"/><path d="M0.5 0.8L6 5l5.5-4.2" fill="none" stroke="#3a3a3a" stroke-width="1"/></svg>Email:&nbsp; info@harbourlightdental.com</span>
      <div class="social"><i></i><i></i><i></i><i></i></div>
    </div>
    <div class="footer-links">Home &nbsp;|&nbsp; Meet the Team &nbsp;|&nbsp; Dental Treatments/Walk-in Treatments &nbsp;|&nbsp; Dental Advice &nbsp;|&nbsp; Contact us</div>
    <div class="footer-copy">Copyright © 2016 The Harbourlight Dental centre.&nbsp; All rights reserved.</div>
    <div class="booking"><span>Appointment Booking</span><span class="booking-name"><i></i>clinic tidal</span></div>
  </div>
</footer>
</body>
</html>
```